Real Estate stationery - need an interesting, eye catching design

I need a letterhead and #10 envelope design in the same theme.
I am looking for an interesting, eye catching design that would stand out in the crowd. I am in the real estate business(which is very competitive) in Florida so standing out and being different is very important to me.
Marguerite(Rita) Delacourt (name), RealtorĀ® (title), 352-608-2147 (cell), bayviewritahomes@quellmail.com (email), www.bayviewritahomes.com(website), 915 Calloway Creek Blvd.,Ste. 3140, Longwood, FL 32779 (business address)

```html
<!DOCTYPE html>
<html lang="en">
<head>
<meta charset="utf-8">
<title>Bayview Realty Stationery</title>
<link href="https://fonts.googleapis.com/css2?family=Poppins:wght@300;400;500&family=Roboto:wght@400&display=swap" rel="stylesheet">
<style>
  :root{
    --backdrop:#dcdcdc;
    --paper:#fafafa;
    --brown:#7a5426;
    --slate:#86868a;
    --ink:#4a4a4a;
    --body-ink:#6a6a6a;
  }
  *{margin:0;padding:0;box-sizing:border-box}
  html,body{width:1200px;height:843px;overflow:hidden;background:var(--backdrop)}
  body{position:relative;font-family:"Poppins",sans-serif;color:var(--ink)}

  .sheet{position:absolute;background:linear-gradient(90deg,#fff,#f3f3f3);box-shadow:0 2px 8px rgba(0,0,0,.18);overflow:hidden}

  /* letterhead */
  .letterhead{left:74px;top:61px;width:508px;height:715px}
  .brand{position:absolute;display:flex;align-items:center;gap:6px;color:var(--brown);font-family:"Poppins",sans-serif;font-weight:500;font-size:16px;white-space:nowrap}
  .brand-mark{width:9px;height:9px;background:var(--brown)}
  .letterhead .brand{left:44px;top:90px}
  .divider{position:absolute;left:344px;top:63px;width:1px;height:54px;background:#b9b9b9}
  .contact{position:absolute;left:354px;top:66px;font-family:"Roboto",sans-serif;font-size:7px;line-height:9px;color:var(--ink);font-style:normal}
  .contact .row{display:flex;align-items:center;gap:4px;margin-top:1px}
  .contact .gap{height:4px}
  .contact svg{flex:none}
  .salutation{position:absolute;left:44px;top:200px;font-weight:300;font-size:13px;color:#444}
  .body-copy{position:absolute;left:44px;top:238px;width:422px;font-weight:300;font-size:6.8px;line-height:11px;color:var(--body-ink)}
  .body-copy p{margin-bottom:11px}
  .closing{position:absolute;left:44px;top:469px;font-weight:300;font-size:6.8px;color:var(--body-ink)}
  .signature{position:absolute;left:40px;top:498px;width:92px;height:38px;background:linear-gradient(90deg,rgba(122,84,38,.18),rgba(122,84,38,.05));border-radius:3px}

  .footer-band{position:absolute;left:0;right:0;bottom:0;height:25px;background:var(--brown)}
  .footer-band::after{content:"";position:absolute;right:0;top:0;bottom:0;width:78px;background:var(--slate)}
  .website{position:absolute;top:0;line-height:25px;color:#fff;font-family:"Roboto",sans-serif;font-size:7px;letter-spacing:1.6px;z-index:1}
  .letterhead .website{left:124px}

  /* envelopes */
  .envelope-back{left:621px;top:275px;width:511px;height:232px}
  .flap{position:absolute;left:0;top:0;width:511px;height:72px}
  .envelope-front{left:621px;top:543px;width:511px;height:232px}
  .envelope-front .brand{left:25px;top:27px}
  .return-address{position:absolute;left:25px;top:74px;width:140px;text-align:center;font-family:"Roboto",sans-serif;font-size:7px;line-height:9px;color:var(--ink);font-style:normal}
  .envelope-front .website{left:120px}
</style>
</head>
<body>

<section class="sheet letterhead" aria-label="Letterhead">
  <div class="brand"><span class="brand-mark"></span>Bayview Realty</div>
  <div class="divider"></div>
  <address class="contact">
    915 Calloway Creek Blvd.,<br>Ste. 3140<br>Cedar Hollow, FL 34712
    <div class="gap"></div>
    <div class="row">
      <svg width="5" height="7" viewBox="0 0 5 7"><rect x=".5" y=".5" width="4" height="6" rx=".8" fill="none" stroke="#7a5426"/></svg>
      352-608-2147
    </div>
    <div class="row">
      <svg width="6" height="5" viewBox="0 0 6 5"><rect width="6" height="5" fill="#7a5426"/><path d="M0 0 3 2.5 6 0" stroke="#fff" stroke-width=".6" fill="none"/></svg>
      bayviewritahomes@quellmail.com
    </div>
  </address>

  <p class="salutation">Dear Mr. Hale,</p>
  <div class="body-copy">
    <p>Lorem ipsum dolor sit amet, consectetur adipiscing elit. Donec orci purus, luctus vitae dignissim eu, iaculis sed purus. Vivamus faucibus, ipsum nec aliquet viverra, leo mauris condimentum ligula, sit amet sagittis enim ligula quis arcu. Nam egestas tortor id nisi porttitor mattis. In tortor ante, ultricies in suscipit a, tempus non massa. Vivamus et auctor mi. Fusce vel massa nulla. Phasellus nec eros mauris, et scelerisque orci.</p>
    <p>Donec malesuada orci vitae nulla accumsan porta a id massa. Quisque accumsan iaculis magna sit amet fringilla. Maecenas consequat, magna eget tincidunt semper, odio nibh rutrum mi, id feugiat ante nisi eu risus. Vestibulum nunc orci, rhoncus a placerat in, ultricies in mi. Cras mattis varius eros, vel fringilla nisi suscipit eget. Quisque scelerisque sagittis nulla at porttitor.</p>
    <p>Sed id augue vitae urna euismod commodo aliquet a quam. Pellentesque arcu velit, cursus et malesuada ut, consequat et diam. Nullam erat sem, rhoncus id ullamcorper vitae, rhoncus et arcu. In ultricies ultricies nulla, ut rutrum nisi iaculis at. Donec eu magna a metus ornare faucibus. Fusce aliquet faucibus ultricies. Morbi semper, est id tincidunt gravida, sem arcu adipiscing lacus, ac bibendum nulla leo eu purus. Quisque nec diam sed risus consectetur a ccumsan quis quis nibh. Vestibulum id purus lorem.</p>
    <p>It is a long established fact that a reader will be distracted by the readable content of a page when looking at its layout. The point of using Lorem Ipsum is that it has a more-or-less normal distribution of letters, as opposed to using 'Content here, content here', making it look like readable English. Many desktop publishing packages</p>
  </div>
  <p class="closing">Sincerely,</p>
  <div class="signature" role="img" aria-label="Handwritten signature of Arthur Hale"></div>

  <div class="footer-band"><span class="website">www.bayviewritahomes.com</span></div>
</section>

<section class="sheet envelope-back" aria-label="Envelope back">
  <svg class="flap" viewBox="0 0 511 72" aria-hidden="true">
    <path d="M0 0H511L503 40Q498 72 466 72H45Q13 72 8 40Z" fill="#7a5426"/>
  </svg>
</section>

<section class="sheet envelope-front" aria-label="Envelope front">
  <div class="brand"><span class="brand-mark"></span>Bayview Realty</div>
  <address class="return-address">915 Calloway Creek Blvd.,Ste. 3140<br>Cedar Hollow, FL 34712</address>
  <div class="footer-band"><span class="website">www.bayviewritahomes.com</span></div>
</section>

</body>
</html>
```